Business Card For Halvenmoor Financial Consulting

Hi, I would like a business card designed. Bold, modern.
Please use the same design as the logo. I have also attached the website design to see the overall theme.
Wordmark Font
Color: Hex: #01AEF7

```html
<!DOCTYPE html>
<html lang="en">
<head>
<meta charset="utf-8">
<title>Halvenmoor Financial Consulting — Business Card</title>
<link rel="stylesheet" href="https://fonts.googleapis.com/css2?family=Montserrat:wght@400;500;700&display=swap">
<style>
  :root {
    --backdrop: #3a3a3a;
    --card: #172330;
    --card-deep: #131d28;
    --accent: #01aef7;
    --accent-soft: #2f9fd8;
    --ink: #ffffff;
    --ink-muted: #c9d3dc;
    --rule: #2b6f96;
    --emboss: #3e5d78;
  }
  * { box-sizing: border-box; margin: 0; padding: 0; }
  html, body { width: 1200px; height: 801px; overflow: hidden; }
  body {
    background: var(--backdrop);
    font-family: "Montserrat", Arial, sans-serif;
    display: flex;
    align-items: center;
    justify-content: center;
    gap: 60px;
  }
  .card {
    width: 520px;
    height: 297px;
    background: var(--card);
    border-bottom: 3px solid var(--accent);
    position: relative;
    overflow: hidden;
  }
  /* Front */
  .brand {
    position: absolute;
    left: 44px;
    top: 48px;
    display: flex;
    align-items: center;
    gap: 14px;
  }
  .brand-square {
    width: 34px;
    height: 34px;
    border: 3px solid var(--accent);
  }
  .brand-name {
    color: var(--ink);
    font-weight: 700;
    font-size: 17px;
    letter-spacing: 2.5px;
    line-height: 1.3;
    text-transform: uppercase;
  }
  .identity {
    position: absolute;
    left: 44px;
    top: 138px;
    width: 190px;
  }
  .person-name {
    color: var(--accent);
    font-weight: 700;
    font-size: 17px;
    letter-spacing: .3px;
    text-transform: uppercase;
  }
  .person-title {
    color: var(--ink);
    font-size: 12px;
    margin-top: 4px;
  }
  .divider {
    position: absolute;
    left: 250px;
    top: 132px;
    width: 1px;
    height: 66px;
    background: var(--rule);
  }
  .contacts {
    position: absolute;
    left: 272px;
    top: 134px;
    list-style: none;
  }
  .contacts li {
    display: flex;
    align-items: center;
    gap: 8px;
    color: var(--ink);
    font-size: 12px;
    line-height: 21px;
  }
  .contacts svg { width: 11px; height: 11px; flex: none; }
  .address {
    position: absolute;
    left: 44px;
    bottom: 34px;
    color: var(--ink);
    font-size: 12px;
    letter-spacing: .2px;
  }
  /* Back */
  .card-back {
    background: linear-gradient(160deg, var(--card) 0%, var(--card-deep) 100%);
    display: flex;
    align-items: center;
    justify-content: center;
  }
  .back-mark {
    display: flex;
    align-items: center;
    gap: 12px;
  }
  .back-square {
    width: 30px;
    height: 30px;
    border: 3px solid var(--emboss);
  }
  .back-name {
    color: var(--emboss);
    font-weight: 700;
    font-size: 16px;
    letter-spacing: 2.5px;
    text-transform: uppercase;
  }
</style>
</head>
<body>
  <section class="card card-front" aria-label="Business card front">
    <div class="brand">
      <div class="brand-square"></div>
      <div class="brand-name">Halvenmoor<br>Financial Consulting</div>
    </div>

    <div class="identity">
      <p class="person-name">Corin Vaelsted</p>
      <p class="person-title">President</p>
    </div>

    <div class="divider"></div>

    <ul class="contacts">
      <li>
        <svg viewBox="0 0 12 12" aria-hidden="true"><path fill="var(--accent)" d="M2.4 1h2l1 2.6-1.3.9a6 6 0 0 0 3.4 3.4l.9-1.3 2.6 1v2c0 .6-.5 1.1-1.1 1.1A9.9 9.9 0 0 1 1.3 2.1C1.3 1.5 1.8 1 2.4 1z"/></svg>
        555-014-2290
      </li>
      <li>
        <svg viewBox="0 0 12 12" aria-hidden="true"><rect x="1" y="2.5" width="10" height="7" rx="1" fill="var(--accent)"/><path d="M1.5 3l4.5 3.5L10.5 3" fill="none" stroke="var(--card)" stroke-width="1"/></svg>
        corin@halvenmoor.com
      </li>
      <li>
        <svg viewBox="0 0 12 12" aria-hidden="true"><circle cx="6" cy="6" r="5" fill="none" stroke="var(--accent)" stroke-width="1.3"/><ellipse cx="6" cy="6" rx="2" ry="5" fill="none" stroke="var(--accent)" stroke-width="1"/><path d="M1 6h10" stroke="var(--accent)" stroke-width="1"/></svg>
        www.halvenmoor.com
      </li>
    </ul>

    <p class="address">1840 Larkspur Harbor Dr, Westbay CA 90412</p>
  </section>

  <section class="card card-back" aria-label="Business card back">
    <div class="back-mark">
      <div class="back-square"></div>
      <span class="back-name">Halvenmoor</span>
    </div>
  </section>
</body>
</html>
```